Business Card Design 2018 Kestrel Machining

Hello,

We need a business card design to reflect our new website we just had designed ( http://www.kestrelmachining.ca/)

We are a growing machine shop looking to grow our clientele and are hoping to update our current business card design to match our website and industry

The colours and design of our website should match to achieve what we are looking for.

I have attached a few images for reference as well as our logo and ISO 9000 needs to be apparent on the card as well

Please let me know what you have :)
Please copy marla@kestrelmachining.ca on all communication regarding this project

Thanks !!!

Industry/Entity Type

Business

Contact Information for Business Card

Company Name, employee name and title and contact details

Colors
f78f20
ffffff
00a990

Requirements
Must have
• Our logo, Iso 9000 same colours as our website http://www.kestrelmachining.ca/

```html
<!DOCTYPE html>
<html lang="en">
<head>
<meta charset="utf-8">
<title>Kestrel Machining – Business Card</title>
<link href="https://fonts.googleapis.com/css2?family=Roboto:wght@400;700&family=Roboto+Condensed:wght@400&display=swap" rel="stylesheet">
<style>
  :root {
    --bg: #e9e7e3;
    --paper: #ffffff;
    --ink: #2b2b2b;
    --muted: #555555;
    --rule: #8a8a8a;
    --teal: #1fb0b5;
    --teal-light: #3cc7cc;
    --teal-dark: #12979c;
  }
  * { margin: 0; padding: 0; box-sizing: border-box; }
  html, body { width: 1200px; height: 886px; overflow: hidden; }
  body {
    background: var(--bg);
    font-family: "Roboto", Arial, sans-serif;
    display: flex;
    align-items: center;
    justify-content: center;
    gap: 56px;
  }
  .card {
    position: relative;
    width: 540px;
    height: 310px;
    border-radius: 3px;
    box-shadow: 0 10px 26px rgba(0,0,0,.22);
    overflow: hidden;
  }
  .card--front { background: var(--paper); color: var(--ink); }
  .card--back {
    background: radial-gradient(ellipse at 50% 45%, var(--teal-light) 0%, var(--teal) 45%, var(--teal-dark) 100%);
    color: #fff;
  }

  .wordmark {
    display: flex;
    align-items: center;
    gap: 10px;
    font-weight: 700;
    text-transform: uppercase;
    letter-spacing: 1px;
  }
  .wordmark__mark { width: 26px; height: 26px; flex: none; }
  .card--front .wordmark { position: absolute; left: 44px; top: 52px; font-size: 30px; color: var(--ink); }
  .card--front .wordmark__mark { background: var(--teal); }
  .card--back .wordmark { position: absolute; left: 50%; top: 50%; transform: translate(-50%, -50%); font-size: 34px; color: #fff; }
  .card--back .wordmark__mark { background: #fff; }

  .identity {
    position: absolute;
    left: 44px; right: 0; top: 150px;
    display: flex;
    align-items: center;
    gap: 12px;
    font-family: "Roboto Condensed", Arial, sans-serif;
  }
  .identity__rule { height: 1px; background: var(--rule); }
  .identity__rule--lead { width: 80px; }
  .identity__rule--tail { flex: 1; }
  .identity__name { color: var(--teal); font-size: 22px; text-transform: uppercase; }
  .identity__title { color: var(--ink); font-size: 15px; text-transform: uppercase; }

  .contacts {
    position: absolute;
    left: 44px; bottom: 40px;
    list-style: none;
    font-size: 13px;
    color: var(--muted);
    line-height: 1.55;
  }
  .contacts li { display: flex; align-items: center; gap: 8px; }
  .contacts svg { width: 11px; height: 11px; fill: var(--teal); flex: none; }

  .location {
    position: absolute;
    right: 40px; bottom: 40px;
    text-align: left;
    font-size: 13px;
    color: var(--muted);
    line-height: 1.55;
  }
  .location__web { color: var(--teal); }

  .badges {
    position: absolute;
    right: 26px; bottom: 24px;
    display: flex;
    flex-direction: column;
    align-items: flex-end;
    gap: 10px;
  }
  .badge { background: rgba(255,255,255,.85); }
  .badge--cert { width: 50px; height: 24px; border-radius: 12px; }
  .badge--listing { width: 46px; height: 18px; }
</style>
</head>
<body>
  <section class="card card--front" aria-label="Business card front">
    <div class="wordmark"><span class="wordmark__mark"></span>Kestrel Machining</div>

    <div class="identity">
      <span class="identity__rule identity__rule--lead"></span>
      <span class="identity__name">Dana Whitford</span>
      <span class="identity__title">– CEO/Founder</span>
      <span class="identity__rule identity__rule--tail"></span>
    </div>

    <ul class="contacts">
      <li><svg viewBox="0 0 12 12"><path d="M2.5 0.5l2 2.5-1 1.2c.6 1.5 1.8 2.7 3.3 3.3l1.2-1 2.5 2-1 2C5 10.5 1.5 7 .5 1.5z"/></svg>604 218 7731</li>
      <li><svg viewBox="0 0 12 12"><path d="M1 1h10v10H1zM2 2v8h8V2z"/></svg>604 355 0192</li>
      <li><svg viewBox="0 0 12 12"><path d="M0 2h12v8H0zM1 3l5 4 5-4z"/></svg>marla@kestrelmachining.ca</li>
    </ul>

    <div class="location">
      <p>412 Foundry Road</p>
      <p>Langley, BC V2Y 1K4</p>
      <p class="location__web">www.kestrelmachining.ca</p>
    </div>
  </section>

  <section class="card card--back" aria-label="Business card back">
    <div class="wordmark"><span class="wordmark__mark"></span>Kestrel Machining</div>
    <div class="badges">
      <span class="badge badge--cert" role="img" aria-label="Quality certification badge"></span>
      <span class="badge badge--listing" role="img" aria-label="Contractor listing badge"></span>
    </div>
  </section>
</body>
</html>
```